Residential Remodeling Contractor needs updated business card

I need a new design for my business card.
Name of the company is Ridgefell Construction. I need a card that commands presence, strength, integrity. I have been in business for 28 years. I am a Residential Remodeling Contractor that covers all aspects of a residential remodel and build.

```html
<!DOCTYPE html>
<html lang="en">
<head>
<meta charset="utf-8">
<title>Ridgefell Construction – Business Card</title>
<link href="https://fonts.googleapis.com/css2?family=Montserrat:wght@400;500;600&display=swap" rel="stylesheet">
<style>
  :root {
    --backdrop: #e7e4de;
    --card-frost: #dedbd5;
    --card-edge: #f3f1ec;
    --navy: #13328a;
    --navy-deep: #0c2570;
    --stripe: #f2ede3;
    --gold: #e3d1ab;
    --cream: #f4efe4;
  }
  html, body {
    margin: 0;
    width: 1200px;
    height: 887px;
    overflow: hidden;
    background: var(--backdrop);
  }
  .canvas {
    position: relative;
    width: 1200px;
    height: 887px;
  }
  .card {
    position: absolute;
    left: 50px;
    top: 143px;
    width: 1100px;
    height: 601px;
    border-radius: 26px;
    background: linear-gradient(135deg, var(--card-edge), var(--card-frost));
    box-shadow: 0 10px 30px rgba(0,0,0,0.12);
    overflow: hidden;
    font-family: "Montserrat", sans-serif;
  }
  .card-bands {
    position: absolute;
    inset: 0;
    width: 1100px;
    height: 601px;
  }
  .holder-name {
    position: absolute;
    right: 62px;
    top: 102px;
    margin: 0;
    color: var(--gold);
    font-size: 37px;
    font-weight: 600;
    letter-spacing: 2px;
    line-height: 1;
  }
  .holder-role {
    position: absolute;
    right: 62px;
    top: 146px;
    margin: 0;
    color: var(--cream);
    font-size: 21px;
    font-weight: 400;
    letter-spacing: 0.5px;
  }
  .company-name {
    position: absolute;
    left: 228px;
    top: 250px;
    margin: 0;
    color: var(--cream);
    font-size: 42px;
    font-weight: 600;
    letter-spacing: 2px;
    line-height: 1.12;
    text-transform: uppercase;
  }
  .contact {
    position: absolute;
    right: 62px;
    top: 362px;
    margin: 0;
    color: var(--gold);
    font-size: 24px;
    font-weight: 400;
    letter-spacing: 0.6px;
    text-align: right;
    font-style: normal;
  }
  .contact-address {
    margin-right: 30px;
    line-height: 31px;
  }
  .contact-lines {
    list-style: none;
    margin: 24px 0 0;
    padding: 0;
  }
  .contact-line {
    display: flex;
    justify-content: flex-end;
    align-items: center;
    gap: 10px;
    height: 32px;
  }
  .contact-icon {
    width: 20px;
    height: 20px;
    flex: none;
  }
</style>
</head>
<body>
<main class="canvas">
  <section class="card" aria-label="Ridgefell Construction business card">
    <svg class="card-bands" viewBox="0 0 982 537" preserveAspectRatio="none" aria-hidden="true">
      <defs>
        <linearGradient id="navyFill" x1="0" y1="0" x2="1" y2="1">
          <stop offset="0" stop-color="var(--navy)"/>
          <stop offset="1" stop-color="var(--navy-deep)"/>
        </linearGradient>
      </defs>
      <polygon points="155,90 982,52 982,168 155,125" fill="url(#navyFill)"/>
      <polygon points="155,125 982,168 982,185 155,142" fill="var(--stripe)"/>
      <polygon points="155,142 982,185 982,537 155,537" fill="url(#navyFill)"/>
    </svg>

    <h1 class="holder-name">MARCUS DELANE</h1>
    <p class="holder-role">Director</p>

    <h2 class="company-name">Ridgefell<br>Construction</h2>

    <address class="contact">
      <div class="contact-address">1208 Hollis Avenue<br>Marietta, GA 30064</div>
      <ul class="contact-lines">
        <li class="contact-line">(770) 555-0148
          <svg class="contact-icon" viewBox="0 0 20 20" aria-hidden="true"><path d="M5 2.5l3 3.5-1.6 1.8c.9 2.2 2.7 4 4.8 4.9l1.8-1.6 3.5 3-1.8 2.6C9.2 16.6 3.4 10.8 2.3 4.3z" fill="none" stroke="var(--gold)" stroke-width="1.6" stroke-linejoin="round"/></svg>
        </li>
        <li class="contact-line">info@ridgefellbuild.com
          <svg class="contact-icon" viewBox="0 0 20 20" aria-hidden="true"><rect x="2" y="4.5" width="16" height="11" rx="1" fill="none" stroke="var(--gold)" stroke-width="1.6"/><polyline points="2.5,5 10,11 17.5,5" fill="none" stroke="var(--gold)" stroke-width="1.6"/></svg>
        </li>
        <li class="contact-line">www.ridgefellbuild.com
          <svg class="contact-icon" viewBox="0 0 20 20" aria-hidden="true"><g fill="none" stroke="var(--gold)" stroke-width="1.4"><circle cx="10" cy="10" r="8"/><ellipse cx="10" cy="10" rx="3.5" ry="8"/><line x1="2" y1="10" x2="18" y2="10"/><line x1="3.5" y1="6" x2="16.5" y2="6"/><line x1="3.5" y1="14" x2="16.5" y2="14"/></g></svg>
        </li>
      </ul>
    </address>
  </section>
</main>
</body>
</html>
```